I need a business card for my original fine art pieces

I would like a business card design including a logo design for a new business in the art world. I am based in the Hunter Valley NSW Australia. I am a contemporary figurative, encaustic and wildlife artist. I would like to be able to upload my email and mobile number to this as well. This design should be one that I can incorporate into banners and flyers etc. Id like to incorporate one of my own images or partial image into the background or somewhere below. My initials are RJ and I would like these used as a logo type. I would like the use of some colour and it to be bright and catchy. The final design should communicate artwork custom made and commissions available.

Overview: Original Fine Artworks for sale, online, art galleries etc, Custom made to order and by commission.

Target market is world wide audience and corporate world

My figurative work is painted using acrylics in a lot of natural ochre colours that reflect the Australian Outback, on canvas, linen, paper or board: My encaustic work is created in a contemporary abstract style using a blow torch and a made with a medium of 100% pure bees wax, Damar resin, mixed media and coloured pigments, applied to Birch board. My wildlife are created using coloured pencil and mixed media on a variety of paper types or board.

```html
<!DOCTYPE html>
<html lang="en">
<head>
<meta charset="utf-8">
<title>Rhea Jansen – Business Card</title>
<link rel="stylesheet" href="https://fonts.googleapis.com/css2?family=Marcellus+SC&family=Arimo:wght@400&family=Open+Sans:wght@400;600&display=swap">
<style>
  :root {
    --backdrop: #5b5b5b;
    --orange: #ec5a24;
    --white: #ffffff;
    --charcoal: #1d1d1d;
    --rule: #bfbfbf;
    --text-light: #f2f2f2;
  }
  * { box-sizing: border-box; margin: 0; padding: 0; }
  html, body { width: 1200px; height: 864px; overflow: hidden; }
  body {
    background: var(--backdrop);
    position: relative;
    font-family: "Open Sans", Arial, sans-serif;
  }
  .card {
    position: absolute;
    left: 300px;
    width: 600px;
    height: 343px;
    box-shadow: 0 6px 18px rgba(0,0,0,0.35);
  }
  .card--front { top: 48px; background: var(--orange); color: var(--white); }
  .card--back { top: 464px; background: var(--charcoal); color: var(--text-light); }

  .lockup { position: absolute; text-align: center; }
  .lockup__mark {
    display: block;
    margin: 0 auto;
    border-radius: 50%;
    border: 3px solid currentColor;
  }
  .lockup__name {
    font-family: "Marcellus SC", "Optima", serif;
    font-weight: 400;
    letter-spacing: 1px;
    white-space: nowrap;
  }
  .lockup__tagline {
    font-family: "Arimo", Arial, sans-serif;
    letter-spacing: 4.5px;
    white-space: nowrap;
  }

  .card--front .lockup { left: 0; right: 0; top: 78px; }
  .card--front .lockup__mark { width: 100px; height: 100px; }
  .card--front .lockup__name { font-size: 44px; line-height: 1; margin-top: 10px; }
  .card--front .lockup__tagline { font-size: 15px; margin-top: 2px; }

  .card--back .lockup { left: 56px; top: 28px; color: var(--orange); }
  .card--back .lockup__mark { width: 84px; height: 84px; }
  .card--back .lockup__name { font-size: 36px; line-height: 1; margin-top: 8px; }
  .card--back .lockup__tagline { font-size: 12.5px; margin-top: 2px; color: var(--text-light); letter-spacing: 3.8px; }

  .divider {
    position: absolute; left: 0; right: 0; top: 172px;
    height: 1px; background: var(--rule);
  }
  .person { position: absolute; right: 70px; top: 188px; }
  .person__name { font-weight: 600; font-size: 19px; color: var(--orange); letter-spacing: 0.5px; }
  .person__role { font-size: 13px; text-transform: uppercase; margin-top: -2px; }

  .address {
    position: absolute; left: 46px; top: 252px;
    font-size: 13px; line-height: 1.5; text-transform: uppercase;
  }
  .contacts {
    position: absolute; right: 52px; top: 262px;
    list-style: none; font-size: 14px; line-height: 1.45;
    text-transform: uppercase; text-align: right;
  }
  .contacts li { display: flex; justify-content: flex-end; align-items: center; gap: 10px; }
  .contacts svg { width: 11px; height: 11px; fill: var(--orange); }
</style>
</head>
<body>
  <section class="card card--front" aria-label="Card front">
    <div class="lockup">
      <span class="lockup__mark" aria-hidden="true"></span>
      <div class="lockup__name">Rhea Jansen</div>
      <div class="lockup__tagline">ORIGINAL FINE ARTWORKS</div>
    </div>
  </section>

  <section class="card card--back" aria-label="Card back">
    <div class="lockup">
      <span class="lockup__mark" aria-hidden="true"></span>
      <div class="lockup__name">Rhea Jansen</div>
      <div class="lockup__tagline">ORIGINAL FINE ARTWORKS</div>
    </div>
    <div class="divider"></div>
    <div class="person">
      <div class="person__name">ALEX CARTER</div>
      <div class="person__role">General Manager</div>
    </div>
    <address class="address" style="font-style:normal">
      1420 Maple Street NE,<br>
      Edmonton, Alberta, T5K 2B1
    </address>
    <ul class="contacts">
      <li>(555) 010-2468
        <svg viewBox="0 0 24 24" aria-hidden="true"><path d="M6.6 10.8a15 15 0 0 0 6.6 6.6l2.2-2.2a1 1 0 0 1 1-.25 11.4 11.4 0 0 0 3.6.57 1 1 0 0 1 1 1V20a1 1 0 0 1-1 1A17 17 0 0 1 3 4a1 1 0 0 1 1-1h3.5a1 1 0 0 1 1 1c0 1.25.2 2.45.57 3.6a1 1 0 0 1-.25 1z"/></svg>
      </li>
      <li>hello@studioname.com
        <svg viewBox="0 0 24 24" aria-hidden="true"><path d="M2 5h20v14H2z M2 5l10 8 10-8" fill="var(--orange)"/><path d="M3 6l9 7 9-7" fill="none" stroke="var(--charcoal)" stroke-width="1.6"/></svg>
      </li>
      <li>www.studiosite.com
        <svg viewBox="0 0 24 24" aria-hidden="true"><circle cx="12" cy="12" r="10"/><path d="M2 12h20M12 2c3 3 3 17 0 20M12 2c-3 3-3 17 0 20" fill="none" stroke="var(--charcoal)" stroke-width="1.4"/></svg>
      </li>
    </ul>
  </section>
</body>
</html>
```